Steadfast Field Crews

We are a underground coal mining labour hire company, needing a website that links into our online payroll (www.wagelinkr.com.au) and also need to have job applications page that is a preform with drop down menu,s with answers or check boxes. We would also need a 3 tier administration access for access to different files.
We are looking for an ongoing relationship with future app integration

Reason: There are a few more designs to come and I'm out at the mine for another week

Industry/Entity Type

Coal Mining

```html
<!DOCTYPE html>
<html lang="en">
<head>
<meta charset="utf-8">
<title>Steadfast Field Crews</title>
<link href="https://fonts.googleapis.com/css2?family=Open+Sans:wght@400;600;700&display=swap" rel="stylesheet">
<style>
:root{
  --orange:#f07d1a;
  --orange-dark:#d9620a;
  --header-top:#2c2c2c;
  --header-bottom:#111;
  --nav-light:#f7f7f7;
  --nav-dark:#e2e2e2;
  --text:#555;
  --text-dark:#333;
  --footer:#444;
  --footer-text:#ddd;
  --panel:#f7f7f7;
}
*{box-sizing:border-box;margin:0;padding:0}
html,body{width:1166px;height:1200px;overflow:hidden}
body{font-family:"Open Sans",Arial,sans-serif;color:var(--text);background:#fff;position:relative}
.site-header{position:absolute;top:0;left:0;width:1166px;height:149px;background:linear-gradient(180deg,var(--header-top),var(--header-bottom))}
.brand{position:absolute;left:140px;top:40px;display:flex;align-items:center;gap:16px}
.brand-mark{width:66px;height:66px;border-radius:50%;border:4px solid #fff}
.brand-name{font-size:44px;font-weight:600;color:#fff;letter-spacing:1px}
.brand-sub{position:absolute;left:140px;top:112px;font-size:10px;color:#fff;opacity:.8}
.contact{position:absolute;right:126px;top:48px;text-align:left;color:#fff}
.contact .call{font-size:19px}
.contact .call strong{color:var(--orange);font-size:23px;font-weight:400}
.contact .email{font-size:13px;margin-top:8px}
.contact .email span{color:var(--orange)}
.main-nav{position:absolute;top:149px;left:0;width:1166px;height:48px;background:linear-gradient(180deg,var(--nav-light),var(--nav-dark));border-bottom:1px solid #ccc}
.main-nav ul{list-style:none;display:flex;position:absolute;left:154px;top:0;height:48px}
.main-nav li{font-size:13px;color:var(--text-dark);height:48px;line-height:50px;padding:0 26px}
.main-nav li.active{background:var(--orange);color:#fff}
.hero{position:absolute;top:197px;left:0;width:1166px;height:367px;background:linear-gradient(120deg,#6b5a48 0%,#c9a585 25%,#e08a4a 45%,#b9c4cc 60%,#d89060 80%,#7a5a40 100%)}
.slider-dots{position:absolute;left:543px;top:335px;display:flex;gap:5px}
.slider-dots span{width:16px;height:16px;border-radius:50%;background:#000}
.slider-dots span.on{background:var(--orange)}
.welcome{position:absolute;top:580px;left:127px;width:670px}
.section-title{font-size:20px;font-weight:400;color:var(--orange)}
.welcome p{font-size:12px;line-height:22.5px;margin-top:7px}
.welcome p+p{margin-top:8px}
.apply-box{position:absolute;left:825px;top:585px;width:216px;height:130px;border:3px solid #eee;background:linear-gradient(135deg,#f08a2a,#d9620a);text-align:center;color:#fff}
.apply-box h2{font-size:26px;font-weight:600;line-height:29px;margin-top:18px;letter-spacing:.5px}
.apply-box .btn{display:inline-block;margin-top:9px;background:#222;color:#fff;font-size:11px;padding:6px 20px;border-radius:2px}
.news{position:absolute;left:126px;top:759px;width:214px;height:303px;background:var(--panel);border:1px solid #ddd}
.news h3{background:linear-gradient(180deg,#3a3a3a,#1a1a1a);color:#fff;font-size:16px;font-weight:400;padding:4px 13px;height:30px}
.news-item{margin:0 13px;padding:12px 0 8px;border-bottom:1px dashed #f0a060}
.news-item:last-of-type{border-bottom:none;padding-top:8px}
.news-item h4{font-size:13px;font-weight:400;color:var(--orange);line-height:18px}
.news-item p{font-size:11.5px;line-height:18px;margin-top:3px}
.news .btn{position:absolute;left:13px;top:259px;background:var(--orange);color:#fff;font-size:11.5px;padding:4px 13px;border-radius:2px;letter-spacing:.5px}
.feature{position:absolute;top:761px;width:192px}
.feature .photo{margin-top:8px;height:116px;border-radius:3px}
.feature p{font-size:11.5px;line-height:19.5px;margin-top:15px}
.feature .more{font-size:10px;color:var(--orange);margin-top:11px;letter-spacing:.3px}
.site-footer{position:absolute;top:1085px;left:0;width:1166px;height:115px;background:var(--footer)}
.footer-links{position:absolute;left:124px;top:22px;font-size:12px;color:var(--footer-text)}
.footer-links span{margin:0 5px;color:#aaa}
.copyright{position:absolute;left:125px;top:65px;font-size:10.5px;color:#999}
.copyright b{color:#eee;font-weight:400}
.payroll{position:absolute;left:729px;top:22px;font-size:28px;color:#ccc;display:flex;align-items:center;gap:6px}
.payroll i{width:22px;height:22px;background:#ccc;display:inline-block}
.social{position:absolute;left:938px;top:29px;display:flex;gap:7px}
.social span{width:30px;height:30px;border-radius:3px}
</style>
</head>
<body>
<header class="site-header">
  <div class="brand">
    <div class="brand-mark"></div>
    <div class="brand-name">SFC</div>
  </div>
  <div class="brand-sub">Steadfast Field Crews</div>
  <div class="contact">
    <div class="call">Call Us: <strong>12 480 2200</strong></div>
    <div class="email">Email: <span>info@sfcfield.com.au</span></div>
  </div>
</header>
<nav class="main-nav">
  <ul>
    <li class="active">HOME</li><li>APPLY FOR POSITION</li><li>PAY PORTAL</li><li>DOWNLOAD</li><li>MISSION</li><li>ABOUT US</li><li>CONTACT US</li>
  </ul>
</nav>
<section class="hero" role="img" aria-label="Two smiling mine workers in hard hats and safety glasses beside heavy chains">
  <div class="slider-dots"><span class="on"></span><span></span><span></span><span></span></div>
</section>
<section class="welcome">
  <h1 class="section-title">Welcome to Our Website</h1>
  <p>We are MKRT pty ltd trading as Steadfast Field Crews, &nbsp;we are experienced in ground consolidation in underground coal mines, &nbsp;in short when they collapse or cave in we come in with chemical pumps and stabilise the ground or fill cavities which will then allow for the mining process to continue. We also do general mine labor as well.</p>
  <p>We are a labor hire company for major mining services company, &nbsp;we offer labor solutions in New South Wales and Queensland in the underground coal mines.</p>
</section>
<aside class="apply-box">
  <h2>APPLY FOR<br>POSITION</h2>
  <span class="btn">APPLY NOW</span>
</aside>
<aside class="news">
  <h3>Latest News</h3>
  <div class="news-item"><h4>Aliquam molestie, mi et imperdiet euismod..</h4><p>Sed accumsan sollicitudin sapien, sit amet adipiscing turpis gravida ac...</p></div>
  <div class="news-item"><h4>Aliquam molestie, mi et imperdiet euismod..</h4><p>Sed accumsan sollicitudin sapien, sit amet adipiscing turpis gravida ac...</p></div>
  <span class="btn">READ ALL</span>
</aside>
<article class="feature" style="left:371px">
  <h2 class="section-title">Services</h2>
  <div class="photo" role="img" aria-label="Continuous mining machine in an underground coal tunnel" style="background:linear-gradient(135deg,#3a3a3a,#8a8a8a 50%,#2a2a2a)"></div>
  <p>Aliquam molestie, mi et imperdiet euismod, dui purus auctor tellus, et interdum lacus lectus et ante. Sed accumsan sollicitudin...</p>
  <div class="more">LEARN MORE &gt;&gt;</div>
</article>
<article class="feature" style="left:609px">
  <h2 class="section-title">Solutions</h2>
  <div class="photo" role="img" aria-label="Mine crew in hard hats watching a controlled fire test underground" style="background:linear-gradient(90deg,#2a2530,#5a3a2a 55%,#e0a030 78%,#2a1a10)"></div>
  <p>Aliquam molestie, mi et imperdiet euismod, dui purus auctor tellus, et interdum lacus lectus et ante. Sed accumsan sollicitudin...</p>
  <div class="more">LEARN MORE &gt;&gt;</div>
</article>
<article class="feature" style="left:847px">
  <h2 class="section-title">Mission</h2>
  <div class="photo" role="img" aria-label="Miner wearing a yellow helmet and headlamp underground" style="background:linear-gradient(135deg,#5a4630,#c9a040 45%,#6a5038)"></div>
  <p>Aliquam molestie, mi et imperdiet euismod, dui purus auctor tellus, et interdum lacus lectus et ante. Sed accumsan sollicitudin...</p>
  <div class="more">LEARN MORE &gt;&gt;</div>
</article>
<footer class="site-footer">
  <div class="footer-links">Home<span>/</span>Apply for Position<span>/</span>Pay Portal<span>/</span>Download<span>/</span>Mission<span>/</span>About us<span>/</span>Contact us</div>
  <div class="copyright">Copyright © 2014. <b>SFC Field.</b> All Right Reserved</div>
  <div class="payroll"><i></i>wagelinkr</div>
  <div class="social" aria-label="Social links">
    <span style="background:#3b5998"></span><span style="background:#4ab3d8"></span><span style="background:#2a7ab0"></span>
  </div>
</footer>
</body>
</html>
```